Business Card Design Project - 2 sided

We need a business card design for a card having one business on each side (ie. two businesses on one card). Would like a design that incorporates logo, tagline and normal fields (name, position, address, phone).

Would also like an allowance for small font text along the bottom (text to be determined, but less than 50 characters).

NB. Attached logo for Harbor Quill has two variations - either can be used.

www.harborquill-example.com / www.velmaro-example.com

```html
<!DOCTYPE html>
<html lang="en">
<head>
<meta charset="utf-8">
<title>Harbor Quill / Velmaro – Business Card</title>
<link rel="stylesheet" href="https://fonts.googleapis.com/css2?family=Open+Sans:wght@400;600;700&display=swap">
<style>
  :root {
    --page-bg: #e9e6e1;
    --card-white: #ffffff;
    --hq-navy: #272561;
    --hq-green: #8cc63f;
    --vm-blue-dark: #1d7bb3;
    --vm-blue-light: #62addb;
    --vm-green: #7bb83a;
    --text-dark: #2a2a2a;
    --text-light: #ffffff;
    --rule-grey: #555555;
  }
  * { box-sizing: border-box; margin: 0; padding: 0; }
  html, body { width: 1200px; height: 402px; overflow: hidden; }
  body {
    background: var(--page-bg);
    font-family: "Open Sans", Arial, sans-serif;
    position: relative;
  }
  .card {
    position: absolute;
    top: 57px;
    width: 512px;
    height: 292px;
    border-radius: 20px;
    overflow: hidden;
    background: var(--card-white);
    box-shadow: 0 2px 6px rgba(0,0,0,0.25);
  }
  .card--harbor { left: 63px; }
  .card--velmaro { left: 626px; }
  .card__art { position: absolute; inset: 0; width: 512px; height: 292px; }

  .brand {
    position: absolute;
    left: 26px;
    top: 82px;
    display: flex;
    align-items: center;
    gap: 10px;
  }
  .brand__dot { width: 26px; height: 26px; border-radius: 50%; }
  .brand__name { font-size: 26px; font-weight: 600; letter-spacing: 0.5px; line-height: 1; }
  .brand__tagline {
    position: absolute;
    font-size: 9.5px;
    font-weight: 600;
    color: var(--text-dark);
  }

  .card--harbor .brand__dot { background: var(--hq-green); }
  .card--harbor .brand__name { color: var(--hq-navy); }
  .card--harbor .brand__tagline { left: 26px; top: 118px; }

  .card--velmaro .brand { top: 66px; }
  .card--velmaro .brand__dot { background: var(--vm-green); }
  .card--velmaro .brand__name { color: var(--vm-blue-dark); font-size: 30px; }
  .card--velmaro .brand__tagline {
    left: 106px; top: 104px; font-size: 12.5px; font-weight: 400;
    letter-spacing: 1px; color: var(--rule-grey);
  }

  .person {
    position: absolute;
    left: 26px;
    top: 218px;
    font-size: 16px;
    font-weight: 700;
  }
  .person__title { font-size: 12px; font-weight: 400; color: var(--text-dark); }
  .card--harbor .person { color: var(--hq-navy); }
  .card--velmaro .person { color: var(--vm-blue-dark); }
  .footnote {
    position: absolute;
    left: 26px;
    top: 248px;
    font-size: 9.5px;
    line-height: 12px;
    color: var(--text-dark);
    letter-spacing: 0.2px;
  }

  .contact {
    position: absolute;
    right: 32px;
    top: 127px;
    text-align: right;
    color: var(--text-light);
    font-size: 12px;
    line-height: 15px;
  }
  .contact__address { margin-bottom: 9px; }
  .contact__line { display: flex; justify-content: flex-end; align-items: center; gap: 4px; height: 17.5px; }
  .contact__icon { width: 10px; height: 10px; fill: var(--text-light); }
</style>
</head>
<body>

  <!-- Side one -->
  <section class="card card--harbor">
    <svg class="card__art" viewBox="0 0 512 292" aria-hidden="true">
      <path d="M360,0 H512 V292 H178 C300,205 378,95 360,0 Z" fill="var(--hq-navy)"/>
      <path d="M328,0 C392,70 332,200 171,292 C296,200 364,92 346,0 Z" fill="var(--hq-green)"/>
    </svg>
    <div class="brand">
      <span class="brand__dot"></span>
      <span class="brand__name">HARBOR QUILL</span>
    </div>
    <p class="brand__tagline">Website Translation and Localisation Specialist...</p>
    <p class="person">Your Name <span class="person__title">/ Title</span></p>
    <p class="footnote">xxxxxxxxxxxxxxxxxxxxxxxxxx<br>xxxxxxxxxxxxxxxxxxxxxxxxxx</p>
    <div class="contact">
      <p class="contact__address">Complex<br>Street,City<br>State, zip code</p>
      <p class="contact__line">123-456-7890 <svg class="contact__icon" viewBox="0 0 10 10"><circle cx="5" cy="5" r="5"/></svg></p>
      <p class="contact__line">123-456-7890 <svg class="contact__icon" viewBox="0 0 10 10"><rect x="2.5" y="0" width="5" height="10" rx="1"/></svg></p>
      <p class="contact__line">123-456-7890 <svg class="contact__icon" viewBox="0 0 10 10"><rect x="0" y="3" width="10" height="7" rx="1"/><rect x="2" y="0" width="6" height="3"/></svg></p>
      <p class="contact__line">name@website.com <svg class="contact__icon" viewBox="0 0 10 10"><rect x="0" y="1.5" width="10" height="7" rx="1"/></svg></p>
      <p class="contact__line">www.website.com <svg class="contact__icon" viewBox="0 0 10 10"><circle cx="5" cy="5" r="5"/></svg></p>
    </div>
  </section>

  <!-- Side two -->
  <section class="card card--velmaro">
    <svg class="card__art" viewBox="0 0 512 292" aria-hidden="true">
      <defs>
        <linearGradient id="velmaroPanel" x1="0" y1="1" x2="1" y2="0">
          <stop offset="0" stop-color="var(--vm-blue-light)"/>
          <stop offset="1" stop-color="var(--vm-blue-dark)"/>
        </linearGradient>
      </defs>
      <path d="M360,0 H512 V292 H178 C300,205 378,95 360,0 Z" fill="url(#velmaroPanel)"/>
      <path d="M328,0 C392,70 332,200 171,292 C296,200 364,92 346,0 Z" fill="var(--vm-green)"/>
    </svg>
    <div class="brand">
      <span class="brand__dot"></span>
      <span class="brand__name">Velmaro</span>
    </div>
    <p class="brand__tagline">Professional SEO Services</p>
    <p class="person">Your Name <span class="person__title">/ Title</span></p>
    <p class="footnote">xxxxxxxxxxxxxxxxxxxxxxxxxx<br>xxxxxxxxxxxxxxxxxxxxxxxxxx</p>
    <div class="contact">
      <p class="contact__address">Complex<br>Street,City<br>State, zip code</p>
      <p class="contact__line">123-456-7890 <svg class="contact__icon" viewBox="0 0 10 10"><circle cx="5" cy="5" r="5"/></svg></p>
      <p class="contact__line">123-456-7890 <svg class="contact__icon" viewBox="0 0 10 10"><rect x="2.5" y="0" width="5" height="10" rx="1"/></svg></p>
      <p class="contact__line">123-456-7890 <svg class="contact__icon" viewBox="0 0 10 10"><rect x="0" y="3" width="10" height="7" rx="1"/><rect x="2" y="0" width="6" height="3"/></svg></p>
      <p class="contact__line">name@website.com <svg class="contact__icon" viewBox="0 0 10 10"><rect x="0" y="1.5" width="10" height="7" rx="1"/></svg></p>
      <p class="contact__line">www.website.com <svg class="contact__icon" viewBox="0 0 10 10"><circle cx="5" cy="5" r="5"/></svg></p>
    </div>
  </section>

</body>
</html>
```